Clean business card with logo provided

I want a card that will stand out among the masses. I need the color and image to show professionalism and yet have a family appeal showing that I only deal with win/win scenarios. The back of the card will be used to take notes about the individual so I can use that in my database entry. I like modern design but need professionalism in it also. It needs to fit my "clean, safe, and affordable housing" motto. I need to be able to write on the file and update the card details for my employees.

Target Market(s)

Investors looking to make investment income through real estate

Industry/Entity Type

Real Estate

Contact Information for Business Card

Brent Kovalich
blank address, city, st, zip code
480-555-3174
brentkovalich@ridgeworthrentals.example
www.ridgeworthrentals.example

Font styles to use
Sans Serif

Requirements
Must have
• I would like the back of the card to have lines for info. example
• Met/Visited: Date:
• Interets:
Nice to have
• I want the cards color to match the logo background color. Font with details to be san serif and black. I want the card rectangular with square corners. Standard business card size. I would like to see cards designed with both images to see which i prefer more.

```html
<!DOCTYPE html>
<html lang="en">
<head>
<meta charset="utf-8">
<title>Ridgeworth Rentals LLC – Business Card</title>
<link href="https://fonts.googleapis.com/css2?family=Lato:wght@400;700;900&display=swap" rel="stylesheet">
<style>
  :root {
    --scene: #3a3a3c;
    --ink: #111213;
    --paper: #f4f5f5;
    --aqua: #2bc3d6;
    --aqua-deep: #12b3ca;
    --aqua-text: #27b7cc;
    --band: #0d0e0f;
    --white: #ffffff;
    --dots: #6b6f72;
  }
  * { box-sizing: border-box; margin: 0; padding: 0; }
  html, body { width: 1200px; height: 900px; overflow: hidden; }
  body {
    background: var(--scene);
    font-family: "Lato", sans-serif;
    position: relative;
  }
  .card {
    position: absolute;
    width: 560px;
    height: 320px;
    overflow: hidden;
    box-shadow: 0 14px 30px rgba(0,0,0,.45);
  }

  /* ---------- back: notes side ---------- */
  .card-back { left: 70px; top: 80px; background: var(--paper); }
  .notes { position: absolute; left: 40px; top: 36px; right: 36px; }
  .note-row {
    display: flex; align-items: flex-end; gap: 8px;
    height: 42px; color: var(--aqua-text); font-size: 19px;
  }
  .note-row .label { white-space: nowrap; }
  .note-row .fill { flex: 1; border-bottom: 2px dotted var(--dots); margin-bottom: 5px; }
  .note-row .label.spaced { margin-left: 14px; }

  .back-band {
    position: absolute; left: 0; right: 0; bottom: 0; height: 34px; background: var(--band);
  }
  .back-band .rule {
    position: absolute; left: 0; right: 24px; top: 10px; height: 1px; background: var(--paper);
  }
  .back-logo {
    position: absolute; left: 0; bottom: 0; width: 370px; height: 100px;
    background: var(--band); padding: 24px 0 0 24px;
  }

  /* ---------- shared wordmark ---------- */
  .wordmark { display: flex; align-items: center; gap: 10px; }
  .wordmark .mark { width: 14px; height: 14px; border-radius: 50%; flex: none; }
  .wordmark .name { font-weight: 700; font-size: 26px; letter-spacing: 1px; white-space: nowrap; line-height: 1.1; }
  .tagline { font-size: 12.5px; margin-top: 6px; letter-spacing: .2px; white-space: nowrap; }

  .back-logo .mark { background: var(--aqua); width: 12px; height: 12px; }
  .back-logo .name { color: var(--aqua); font-size: 21px; }
  .back-logo .tagline { color: var(--aqua); font-size: 12px; margin-top: 8px; }

  /* ---------- front: contact side ---------- */
  .card-front {
    left: 570px; top: 500px;
    background: linear-gradient(160deg, var(--aqua) 0%, var(--aqua-deep) 100%);
  }
  .front-logo { position: absolute; right: 34px; top: 36px; text-align: left; }
  .front-logo .mark { background: var(--white); }
  .front-logo .name { color: var(--white); }
  .front-logo .tagline { color: #0b3b42; }

  .holder {
    position: absolute; left: 34px; top: 120px;
    font-weight: 900; font-size: 28px; color: var(--ink); letter-spacing: .5px;
  }
  .contacts { position: absolute; left: 34px; top: 170px; color: var(--ink); font-size: 15px; }
  .contact { display: flex; align-items: center; gap: 9px; height: 22px; white-space: nowrap; }
  .contact svg { width: 13px; height: 13px; fill: var(--ink); flex: none; }
  .contact.gap { margin-top: 12px; }

  .front-band {
    position: absolute; left: 0; right: 0; bottom: 0; height: 30px; background: var(--band);
  }
  .front-band .rule {
    position: absolute; left: 0; right: 24px; top: 9px; height: 1px; background: var(--aqua);
  }
</style>
</head>
<body>

<section class="card card-back" aria-label="Card back, notes side">
  <div class="notes">
    <div class="note-row"><span class="label">Meet/Visited:</span><span class="fill"></span><span class="label spaced">Time:</span><span class="fill"></span></div>
    <div class="note-row"><span class="label">Date:</span><span class="fill"></span></div>
    <div class="note-row"><span class="label">INTERETS :</span><span class="fill"></span></div>
    <div class="note-row"><span class="fill"></span></div>
  </div>
  <div class="back-band"><span class="rule"></span></div>
  <div class="back-logo">
    <div class="wordmark"><span class="mark"></span><span class="name">RIDGEWORTH RENTALS LLC</span></div>
    <p class="tagline">Providing clean, safe, and affordable housing</p>
  </div>
</section>

<section class="card card-front" aria-label="Card front, contact side">
  <div class="front-logo">
    <div class="wordmark"><span class="mark"></span><span class="name">RIDGEWORTH RENTALS LLC</span></div>
    <p class="tagline">Providing clean, safe, and affordable housing</p>
  </div>

  <h1 class="holder">BRENT KOVALICH</h1>

  <div class="contacts">
    <p class="contact">
      <svg viewBox="0 0 16 16" aria-hidden="true"><path d="M3.5 1h3l1.2 3.4-1.9 1.3a9 9 0 0 0 4.5 4.5l1.3-1.9L15 9.5v3A2.5 2.5 0 0 1 12.5 15 11.5 11.5 0 0 1 1 3.5 2.5 2.5 0 0 1 3.5 1z"/></svg>
      480-555-3174
    </p>
    <p class="contact">
      <svg viewBox="0 0 16 16" aria-hidden="true"><path d="M8 1a7 7 0 1 0 0 14A7 7 0 0 0 8 1zm0 1.5c.8 0 1.8 1.6 2.1 4H5.9c.3-2.4 1.3-4 2.1-4zM2.6 7.5h1.8c.1-1.5.4-2.8.9-3.8a5.5 5.5 0 0 0-2.7 3.8zm0 1h1.8c.1 1.5.4 2.8.9 3.8a5.5 5.5 0 0 1-2.7-3.8zm3.3 0h4.2c-.3 2.4-1.3 4-2.1 4s-1.8-1.6-2.1-4zm5.7 0h1.8a5.5 5.5 0 0 1-2.7 3.8c.5-1 .8-2.3.9-3.8zm0-1c-.1-1.5-.4-2.8-.9-3.8a5.5 5.5 0 0 1 2.7 3.8z"/></svg>
      www.ridgeworthrentals.example
    </p>
    <p class="contact gap">
      <svg viewBox="0 0 16 16" aria-hidden="true"><path d="M1 3h14v10H1zm1.5 1.2v.3L8 8.6l5.5-4.1v-.3zm0 2.2v5.1h11V6.4L8 10.4z"/></svg>
      brentkovalich@ridgeworthrentals.example
    </p>
    <p class="contact">
      <svg viewBox="0 0 16 16" aria-hidden="true"><path d="M8 0.8A5 5 0 0 0 3 5.8c0 3.8 5 9.4 5 9.4s5-5.6 5-9.4a5 5 0 0 0-5-5zm0 7a2 2 0 1 1 0-4 2 2 0 0 1 0 4z"/></svg>
      blank address, city, st, zip code
    </p>
  </div>

  <div class="front-band"><span class="rule"></span></div>
</section>

</body>
</html>
```